New website for concierge mobile medical service

new website for business:
WEBSITE REQUEST LIST:
Luxury product look.
Professional. Clean & simple, NO stock people photos. Graphics OK.
Black and white text.

```html
<!DOCTYPE html>
<html lang="en">
<head>
<meta charset="utf-8">
<title>Lumen Care – Optimal Wellness</title>
<link href="https://fonts.googleapis.com/css2?family=Lato:wght@400;700&display=swap" rel="stylesheet">
<style>
:root{
  --ink:#1e1e1e;
  --white:#ffffff;
  --navy:#062b44;
  --deep:#020a10;
  --heading-blue:#1569a8;
  --accent-purple:#6a56a8;
  --tick-blue:#1b7ac0;
  --teal:#1a7fa0;
  --teal-dark:#17627f;
  --button:#8ad0d8;
  --field-border:#dcdcdc;
  --footer:#222222;
}
*{box-sizing:border-box;margin:0;padding:0}
html,body{width:885px;height:1200px;overflow:hidden;background:var(--white)}
body{position:relative;font-family:'Lato',sans-serif;color:var(--ink)}
.abs{position:absolute}

.site-header{position:absolute;left:0;top:0;width:885px;height:79px;background:var(--white)}
.brand{position:absolute;left:116px;top:15px;width:88px;height:88px;border-radius:50%;background:var(--white);z-index:3;display:flex;align-items:center;justify-content:center}
.brand-mark{width:76px;height:76px;border-radius:50%;background:var(--navy);border:4px solid #4cc4d6;display:flex;align-items:center;justify-content:center;color:var(--white);font-weight:700;font-size:11px;text-align:center;line-height:1.1}
.phone{position:absolute;right:106px;top:12px;display:flex;align-items:center;gap:9px;color:var(--accent-purple);font-weight:700;font-size:14px}
.phone-icon{width:24px;height:24px;background:var(--accent-purple);border-radius:2px;display:flex;align-items:center;justify-content:center}
.main-nav{position:absolute;right:106px;top:55px;display:flex;gap:0}
.main-nav a{font-size:9px;font-weight:700;color:var(--ink);text-decoration:none;padding:0 14px;height:24px;line-height:13px;position:relative}
.main-nav a:last-child{padding-right:0}
.main-nav a.current{color:var(--heading-blue)}
.main-nav a.current::after{content:"";position:absolute;left:0;right:0;bottom:0;height:4px;background:var(--navy)}

.hero{position:absolute;left:0;top:79px;width:885px;height:195px;background:linear-gradient(90deg,var(--deep) 0%,#052438 45%,#0a4a6e 100%)}
.hero-title{position:absolute;left:106px;top:77px;font-size:33px;font-weight:700;color:var(--white)}
.hero-art{position:absolute;left:639px;top:23px;width:150px;height:150px;border-radius:50%;border:3px solid #5fd3e6;background:radial-gradient(circle,#0c4f74,#083c5c)}

.intro{position:absolute;left:107px;top:306px;width:670px}
.intro h2{font-size:16.5px;font-weight:700;color:var(--heading-blue);margin-bottom:6px}
.intro p{font-size:10.3px;line-height:19px}
.intro h3{font-size:13.5px;font-weight:700;color:var(--accent-purple);margin:7px 0 9px}
.goals{position:absolute;top:449px;left:107px;display:grid;grid-template-columns:170px 220px;grid-auto-flow:column;grid-template-rows:repeat(5,23.6px)}
.goals li{list-style:none;display:flex;align-items:center;gap:12px;font-size:10.6px}
.goals svg{flex:none}

.subscribe{position:absolute;left:0;top:595px;width:885px;height:186px;background:linear-gradient(110deg,var(--teal) 0%,var(--teal-dark) 50%,var(--teal) 100%)}
.subscribe h2{position:absolute;left:0;right:0;top:33px;text-align:center;color:var(--white);font-size:24px;font-weight:700}
.field{position:absolute;background:var(--white);font-size:9.2px;padding-left:11px;display:flex;align-items:center;color:var(--ink)}
.field.line{border:1px solid var(--field-border)}
.field.area{align-items:flex-start;padding-top:13px}
.btn{position:absolute;background:var(--button);color:var(--white);font-weight:700;font-size:11.5px;display:flex;align-items:center;justify-content:center}

.contact-title{position:absolute;left:0;right:0;top:808px;text-align:center;font-size:24px;font-weight:700}
.contact-lead{position:absolute;left:0;right:0;top:848px;text-align:center;font-size:12px}

.site-footer{position:absolute;left:0;top:1100px;width:885px;height:100px;background:var(--footer);color:var(--white)}
.footer-nav{position:absolute;left:0;right:0;top:17px;display:flex;justify-content:center;gap:29px}
.footer-nav a{color:var(--white);text-decoration:none;font-size:9.2px;font-weight:700}
.copyright{position:absolute;left:0;right:0;top:42px;text-align:center;font-size:8.4px}
.social{position:absolute;left:0;right:0;top:64px;display:flex;justify-content:center;gap:13px}
.social span{width:12px;height:12px;border-radius:50%;background:var(--white)}
</style>
</head>
<body>

<header class="site-header">
  <div class="brand"><div class="brand-mark">Lumen<br>Care</div></div>
  <div class="phone">
    <span class="phone-icon"><svg width="12" height="12" viewBox="0 0 24 24"><path fill="#fff" d="M6.6 10.8a15.1 15.1 0 0 0 6.6 6.6l2.2-2.2c.3-.3.7-.4 1-.2 1.1.4 2.3.6 3.6.6.6 0 1 .4 1 1V20c0 .6-.4 1-1 1C10.6 21 3 13.4 3 4c0-.6.4-1 1-1h3.5c.6 0 1 .4 1 1 0 1.3.2 2.5.6 3.6.1.3 0 .7-.2 1z"/></svg></span>
    555-014-2290
  </div>
  <nav class="main-nav">
    <a href="#">HOME</a><a href="#">ABOUT US</a><a href="#">WHY LUMEN?</a><a href="#">SERVICE AREA</a><a href="#">OTHER</a><a href="#" class="current">FAQ</a><a href="#">CONTACT US</a>
  </nav>
</header>

<section class="hero">
  <h1 class="hero-title">Optimal Wellness</h1>
  <div class="hero-art" role="img" aria-label="Line illustration of a medical caduceus above a car"></div>
</section>

<section class="intro">
  <h2>Why does Lumen Care include optimal wellness as part of my care</h2>
  <p>As physicians, we believe customized wellness care will give you the plan and tools needed to improve your overall health and vitality. We will help you manage important aspects of your health that contribute to an improved healthspan including longevity and feeling better every day.</p>
  <h3>What does wellness care look like?</h3>
  <p>We will help you set and achieve goals such as:</p>
</section>

<ul class="goals">
  <li><svg width="10" height="10" viewBox="0 0 20 20"><circle cx="10" cy="10" r="10" fill="var(--tick-blue)"/><path d="M5.5 10.2l3 3 6-6" stroke="#fff" stroke-width="2.4" fill="none"/></svg>Weight management</li>
  <li><svg width="10" height="10" viewBox="0 0 20 20"><circle cx="10" cy="10" r="10" fill="var(--tick-blue)"/><path d="M5.5 10.2l3 3 6-6" stroke="#fff" stroke-width="2.4" fill="none"/></svg>Fat loss</li>
  <li><svg width="10" height="10" viewBox="0 0 20 20"><circle cx="10" cy="10" r="10" fill="var(--tick-blue)"/><path d="M5.5 10.2l3 3 6-6" stroke="#fff" stroke-width="2.4" fill="none"/></svg>Nutritional health</li>
  <li><svg width="10" height="10" viewBox="0 0 20 20"><circle cx="10" cy="10" r="10" fill="var(--tick-blue)"/><path d="M5.5 10.2l3 3 6-6" stroke="#fff" stroke-width="2.4" fill="none"/></svg>Age-optimal fitness</li>
  <li><svg width="10" height="10" viewBox="0 0 20 20"><circle cx="10" cy="10" r="10" fill="var(--tick-blue)"/><path d="M5.5 10.2l3 3 6-6" stroke="#fff" stroke-width="2.4" fill="none"/></svg>Hormonal balance</li>
  <li><svg width="10" height="10" viewBox="0 0 20 20"><circle cx="10" cy="10" r="10" fill="var(--tick-blue)"/><path d="M5.5 10.2l3 3 6-6" stroke="#fff" stroke-width="2.4" fill="none"/></svg>Customized supplements / vitamins</li>
  <li><svg width="10" height="10" viewBox="0 0 20 20"><circle cx="10" cy="10" r="10" fill="var(--tick-blue)"/><path d="M5.5 10.2l3 3 6-6" stroke="#fff" stroke-width="2.4" fill="none"/></svg>Stress management</li>
  <li><svg width="10" height="10" viewBox="0 0 20 20"><circle cx="10" cy="10" r="10" fill="var(--tick-blue)"/><path d="M5.5 10.2l3 3 6-6" stroke="#fff" stroke-width="2.4" fill="none"/></svg>Sleep hygiene</li>
  <li><svg width="10" height="10" viewBox="0 0 20 20"><circle cx="10" cy="10" r="10" fill="var(--tick-blue)"/><path d="M5.5 10.2l3 3 6-6" stroke="#fff" stroke-width="2.4" fill="none"/></svg>Smoking cessation</li>
</ul>

<section class="subscribe" role="img" aria-label="Teal background with faint medical hexagon pattern">
  <h2>Subscribe</h2>
  <div class="field" style="left:204px;top:76px;width:234px;height:32px">Enter Name</div>
  <div class="field" style="left:447px;top:76px;width:234px;height:32px">Enter Email Address</div>
  <div class="btn" style="left:204px;top:115px;width:477px;height:33px">SUBSCRIBE NOW</div>
</section>

<h2 class="contact-title">Contact Us</h2>
<p class="contact-lead">We want to hear from you! Click below to send us a message and receive upcoming information.</p>
<div class="field line" style="left:165px;top:877px;width:270px;height:30px">Enter Name</div>
<div class="field line" style="left:452px;top:877px;width:270px;height:30px">Enter Email Address</div>
<div class="field line" style="left:165px;top:916px;width:270px;height:30px">Phone No</div>
<div class="field line" style="left:452px;top:916px;width:270px;height:30px">Subject</div>
<div class="field line area" style="left:165px;top:953px;width:557px;height:74px">Message</div>
<div class="btn" style="left:204px;top:1040px;width:478px;height:33px">SUBMIT NOW</div>

<footer class="site-footer">
  <nav class="footer-nav">
    <a href="#">HOME</a><a href="#">ABOUT US</a><a href="#">WHY LUMEN?</a><a href="#">SERVICE AREA</a><a href="#">OTHER</a><a href="#">CONTACT US</a>
  </nav>
  <p class="copyright">Copyright © 2019.&nbsp; Company Name&nbsp; All Rights Reserved</p>
  <div class="social">
    <span aria-label="Social link 1"></span><span aria-label="Social link 2"></span><span aria-label="Social link 3"></span><span aria-label="Social link 4"></span><span aria-label="Social link 5"></span>
  </div>
</footer>

</body>
</html>
```